Web Design for guards MMJ transport and security services

Harbor Crest Protective solutions a tallow unified company, is looking for a designer to create a website that displays our service portfolio. We need marketing pictures and content to be created in a original and competitive fashion, intriguing to our customers. We will need forms on the website to be created for calendar booking (somehow integrate into exchange if possible) and general inquiry forms. There will need to be pages dedicated to our staff, MMJ trasnport & Courier services, our vehicles, alarm systems, video systems, video monitoring, private investigations, and surveillance aduit and compliance investigations, payment gateway integration, and general company information. I Have attached our main company logo. Also have a emphasis on being state licensed by the Colorado RPB. Have a link to our parent site, tallowcctv.example

Target Market(s)

Colorado Marijuana industry, MMJ transport services, guard services, armed gaurd services.

Contact Information for Business Card

Would like a sleek simple design highlighting what we offer. must match the website and have a overall professional straight to the point appearance.

Number of Pages Required

1 page

Colors
33b8a4
00a990
9bcb3c
acd036
cadf82
85cae6
33a6d7
0792cd

Requirements
Must have
• Easy to use, lots of images, professional.
Nice to have
• Creativity

```html
<!DOCTYPE html>
<html lang="en">
<head>
<meta charset="utf-8">
<title>Harbor Crest Protective Solutions</title>
<link href="https://fonts.googleapis.com/css2?family=Raleway:ital,wght@0,400;0,500;0,600;0,700;1,600;1,700;1,800&display=swap" rel="stylesheet">
<style>
:root{
  --teal:#00a990;
  --teal-soft:#33b8a4;
  --teal-dark:#008a75;
  --green:#acd036;
  --green-dark:#8fb21f;
  --green-mid:#9bcb3c;
  --green-light:#c6dc78;
  --green-light-dark:#a9c25a;
  --blue:#33a6d7;
  --blue-dark:#1d88b8;
  --blue-deep:#0792cd;
  --brand-red:#c0262d;
  --ink:#555;
  --ink-soft:#777;
  --paper:#fff;
  --mist:#f1f1f1;
  --footer:#333;
  --footer-text:#ddd;
}
*{box-sizing:border-box;margin:0;padding:0}
html,body{width:1200px;height:2416px;overflow:hidden}
body{font-family:"Raleway",Arial,sans-serif;background:var(--paper);color:var(--ink);position:relative}
.abs{position:absolute}

/* header */
.top-rule{left:0;top:0;width:1200px;height:5px;background:var(--green)}
.brand{left:74px;top:50px;display:flex;align-items:center;gap:12px}
.brand-mark{width:30px;height:30px;border-radius:50%;background:var(--brand-red)}
.brand-name{font-weight:700;font-size:19px;color:var(--brand-red);line-height:1.15}
.phone{right:72px;top:44px;display:flex;align-items:center;gap:18px;color:var(--teal);font-weight:700;font-style:italic;font-size:27px}
.phone svg{width:38px;height:38px}

/* hero */
.hero{left:0;top:122px;width:1200px;height:538px}
.hero-nav{position:absolute;left:0;top:0;width:406px;height:538px;background:var(--teal)}
.hero-nav ul{list-style:none;padding:37px 0 0 75px}
.hero-nav li{color:#fff;font-size:14.5px;font-weight:600;text-transform:uppercase;height:39.7px;line-height:39.7px;letter-spacing:.2px}
.hero-photo{position:absolute;left:406px;top:0;width:794px;height:538px;background:linear-gradient(135deg,#2c3440 0%,#4b5a6a 40%,#b9c3c9 70%,#7fb6d8 100%)}
.slider-dots{position:absolute;left:29px;top:462px;display:flex;gap:8px}
.slider-dots span{width:12px;height:12px;border-radius:50%;background:#fff}
.slider-dots span.on{background:var(--blue)}

/* welcome */
.welcome{left:78px;top:700px;width:1045px;text-align:center}
.section-title{display:flex;align-items:center;gap:12px;color:var(--blue-deep);font-weight:700;font-style:italic;font-size:26px;text-transform:uppercase}
.welcome .section-title{justify-content:center}
.section-title svg{width:24px;height:26px}
.welcome p{margin-top:18px;font-size:14.5px;line-height:26px;color:var(--ink)}

/* services */
.services-band{left:0;top:905px;width:1200px;height:448px;background:linear-gradient(#eeeeee,#fff 40%)}
.tiles{left:74px;top:955px;display:grid;grid-template-columns:repeat(4,242px);grid-template-rows:repeat(2,177px);column-gap:27px;row-gap:18px}
.tile{display:flex;flex-direction:column;align-items:center;justify-content:center;color:#fff;font-weight:700;font-style:italic;font-size:15.5px;text-transform:uppercase;text-align:center;line-height:22px;border-bottom:5px solid}
.tile svg{width:64px;height:64px;margin-bottom:14px}
.tile--teal{background:var(--teal-soft);border-color:var(--teal-dark)}
.tile--green{background:var(--green);border-color:var(--green-dark)}
.tile--blue{background:var(--blue);border-color:var(--blue-dark)}
.tile--light{background:var(--green-light);border-color:var(--green-light-dark)}

/* info cards */
.cards{left:74px;top:1369px;display:grid;grid-template-columns:repeat(3,330px);column-gap:31px}
.card{height:442px;background:#fff;border:1px solid #e3e3e3;box-shadow:0 1px 3px rgba(0,0,0,.06);padding:18px 17px}
.card-photo{height:177px}
.card h3{margin-top:24px;color:var(--blue-deep);font-weight:700;font-style:italic;font-size:25px;text-transform:uppercase}
.card p{margin-top:8px;font-size:14.5px;line-height:26px;color:var(--ink-soft)}
.btn{display:inline-block;background:linear-gradient(var(--teal-soft),var(--teal));color:#fff;font-weight:700;font-size:14.5px;text-transform:uppercase;width:142px;height:37px;line-height:37px;text-align:center;border-radius:2px}
.card .btn{margin-top:14px}
.card-partner{height:177px;background:#ececec;display:flex;align-items:center;justify-content:center;gap:12px}
.card-partner .dot{width:40px;height:40px;border-radius:50%;background:var(--blue-deep)}
.card-partner span{font-weight:700;font-size:28px;color:var(--blue-deep);text-transform:uppercase}

/* news */
.news-band{left:0;top:1853px;width:1200px;height:301px;background:linear-gradient(#eeeeee,#fff 45%)}
.news-title{left:74px;top:1897px}
.news-arrows{left:1076px;top:1900px;display:flex;gap:6px}
.news-arrows svg{width:22px;height:22px}
.news-item{top:1956px;display:flex;gap:20px}
.news-photo{width:198px;height:145px}
.news-body{width:290px}
.news-body p{font-size:14.5px;line-height:26px;color:var(--ink-soft);margin-top:-3px}
.news-body .btn{margin-top:12px}

/* footer */
.footer{left:0;top:2154px;width:1200px;height:262px;background:var(--footer);color:var(--footer-text)}
.footer-brand{position:absolute;left:74px;top:84px;display:flex;align-items:center;gap:10px}
.footer-brand .brand-mark{width:24px;height:24px}
.footer-brand .brand-name{font-size:16px}
.legal{position:absolute;left:74px;top:163px;font-size:12.5px;line-height:22px}
.footer h4{font-size:12.5px;font-weight:600;color:var(--green);text-transform:uppercase;margin-bottom:8px}
.foot-nav{position:absolute;left:453px;top:43px}
.foot-cols{display:grid;grid-template-columns:248px 200px}
.foot-cols ul{list-style:none}
.foot-cols li{font-size:12.5px;line-height:28px}
.connect{position:absolute;left:905px;top:43px}
.social{display:flex;gap:6px;margin-top:2px}
.social span{width:28px;height:28px;border-radius:50%;background:#fff}
</style>
</head>
<body>

<div class="abs top-rule"></div>

<header>
  <div class="abs brand">
    <span class="brand-mark"></span>
    <span class="brand-name">Harbor Crest</span>
  </div>
  <div class="abs phone">
    <svg viewBox="0 0 38 38" aria-hidden="true"><circle cx="19" cy="19" r="17" fill="none" stroke="#00a990" stroke-width="2.5"/><path d="M14 11c1 0 2 3 2.5 4s-1.5 2-1 3 3 4 4.5 4.5 2-1.5 3-1 4 1.5 4 2.5-2 3-3.5 3c-5 0-12-7-12-12 0-1.5 1.5-4 2.5-4z" fill="#00a990"/></svg>
    <span>1-800-555-0142</span>
  </div>
</header>

<section class="abs hero">
  <nav class="hero-nav">
    <ul>
      <li>Home</li>
      <li>About us</li>
      <li>Our staff</li>
      <li>MMJ trasnport &amp; courier services</li>
      <li>Our vehicles</li>
      <li>Alarm systems</li>
      <li>Video systems</li>
      <li>Video monitoring</li>
      <li>Private investigations</li>
      <li>Surveillance audit</li>
      <li>Compliance investigations</li>
      <li>Contact us</li>
    </ul>
  </nav>
  <div class="hero-photo" role="img" aria-label="Security operator watching a wall of CCTV monitors in a control room">
    <div class="slider-dots"><span class="on"></span><span></span><span></span><span></span></div>
  </div>
</section>

<section class="abs welcome">
  <h2 class="section-title">
    <svg viewBox="0 0 24 26" aria-hidden="true"><path d="M12 2l9 3v7c0 6-4 10-9 12-5-2-9-6-9-12V5z" fill="none" stroke="#0792cd" stroke-width="2"/><path d="M8 12l3 3 5-6" fill="none" stroke="#0792cd" stroke-width="2"/></svg>
    Welcome to our website
  </h2>
  <p>Aliquam molestie, mi et imperdiet euismod, dui purus auctor tellus, et interdum lacus lectus et ante. Sed accumsan sollicitudin sapien, sit amet adipiscing turpis gravida ac. In congue, neque ac lobortis volutpat, libero mauris varius mi, vitae suscipit ipsum ligula vitae risus. Duis aliquam nibh a dui iaculis viverra id a velit. Vivamus egestas risus in magna varius commodo. Sed semper viverra egestas. Etiam pretium porttitor lectus, vel ornare neque porta volutpat.</p>
</section>

<div class="abs services-band"></div>
<section class="abs tiles">
  <div class="tile tile--teal">
    <svg viewBox="0 0 64 64" aria-hidden="true"><rect x="10" y="22" width="34" height="26" fill="none" stroke="#fff" stroke-width="3"/><path d="M10 22l17 13 17-13" fill="none" stroke="#fff" stroke-width="3"/><rect x="46" y="14" width="10" height="40" fill="#fff"/></svg>
    MMJ trasnport<br>&amp; courier services</div>
  <div class="tile tile--green">
    <svg viewBox="0 0 64 64" aria-hidden="true"><rect x="4" y="16" width="36" height="26" fill="#fff"/><path d="M42 24h10l8 9v9H42z" fill="#fff"/><circle cx="14" cy="46" r="5" fill="#fff" stroke="#acd036" stroke-width="2"/><circle cx="50" cy="46" r="5" fill="#fff" stroke="#acd036" stroke-width="2"/></svg>
    Our vehicles</div>
  <div class="tile tile--blue">
    <svg viewBox="0 0 64 64" aria-hidden="true"><circle cx="32" cy="36" r="18" fill="none" stroke="#fff" stroke-width="3"/><circle cx="32" cy="36" r="5" fill="#fff"/><path d="M20 10l4 6M32 6v8M44 10l-4 6" stroke="#fff" stroke-width="3"/></svg>
    Alarm systems</div>
  <div class="tile tile--light">
    <svg viewBox="0 0 64 64" aria-hidden="true"><rect x="8" y="10" width="48" height="44" fill="none" stroke="#fff" stroke-width="3"/><path d="M26 22v20l16-10z" fill="#fff"/></svg>
    Video systems</div>
  <div class="tile tile--blue">
    <svg viewBox="0 0 64 64" aria-hidden="true"><rect x="4" y="10" width="56" height="36" rx="2" fill="none" stroke="#fff" stroke-width="3"/><path d="M18 40V28M26 40V22M34 40V30M42 40V18" stroke="#fff" stroke-width="4"/><path d="M24 54h16M32 46v8" stroke="#fff" stroke-width="3"/></svg>
    Video monitoring</div>
  <div class="tile tile--light">
    <svg viewBox="0 0 64 64" aria-hidden="true"><path d="M12 6h28v36H12z" fill="none" stroke="#fff" stroke-width="3"/><path d="M18 16h16M18 24h10" stroke="#fff" stroke-width="3"/><circle cx="38" cy="38" r="10" fill="none" stroke="#fff" stroke-width="3"/><path d="M45 45l11 11" stroke="#fff" stroke-width="4"/></svg>
    Private<br>investigations</div>
  <div class="tile tile--green">
    <svg viewBox="0 0 64 64" aria-hidden="true"><path d="M12 6h32v52H12z" fill="none" stroke="#fff" stroke-width="3"/><path d="M18 18h20M18 26h20M18 34h20M18 42h14" stroke="#fff" stroke-width="3"/><path d="M50 10v36l3 6 3-6V10z" fill="#fff"/></svg>
    Surveillance audit</div>
  <div class="tile tile--teal">
    <svg viewBox="0 0 64 64" aria-hidden="true"><rect x="12" y="10" width="34" height="44" fill="none" stroke="#fff" stroke-width="3"/><rect x="22" y="6" width="14" height="8" fill="#fff"/><path d="M18 24h20M18 32h20M18 40h12" stroke="#fff" stroke-width="3"/><circle cx="46" cy="46" r="10" fill="#fff"/><path d="M41 46l4 4 6-7" fill="none" stroke="#33b8a4" stroke-width="3"/></svg>
    Compliance<br>investigations</div>
</section>

<section class="abs cards">
  <article class="card">
    <div class="card-photo" role="img" aria-label="Team of security staff in dark business suits" style="background:linear-gradient(#dfe7ee,#4a5260 60%,#2b2f36)"></div>
    <h3>About us</h3>
    <p>Duis aliquam nibh a dui iaculis viverra id a velit. Vivamus egestas risus in magna varius commodo. Sed semper viverra egestas vel ornare...</p>
    <span class="btn">Read more</span>
  </article>
  <article class="card">
    <div class="card-photo" role="img" aria-label="Staff members joining hands in a circle, seen from below" style="background:linear-gradient(135deg,#f3f5f7,#d9b98c 50%,#e9eef2)"></div>
    <h3>Our staff</h3>
    <p>Duis aliquam nibh a dui iaculis viverra id a velit. Vivamus egestas risus in magna varius commodo. Sed semper viverra egestas vel ornare...</p>
    <span class="btn">Read more</span>
  </article>
  <article class="card">
    <div class="card-partner"><span class="dot"></span><span>Tallow Unified</span></div>
    <h3>We are a part of</h3>
    <p>Duis aliquam nibh a dui iaculis viverra id a velit. Vivamus egestas risus in magna varius commodo. Sed semper viverra egestas vel ornare...</p>
    <span class="btn">Read more</span>
  </article>
</section>

<div class="abs news-band"></div>
<h2 class="abs section-title news-title">
  <svg viewBox="0 0 24 26" aria-hidden="true"><path d="M12 2l9 3v7c0 6-4 10-9 12-5-2-9-6-9-12V5z" fill="none" stroke="#0792cd" stroke-width="2"/><path d="M8 12l3 3 5-6" fill="none" stroke="#0792cd" stroke-width="2"/></svg>
  Latest news
</h2>
<div class="abs news-arrows">
  <svg viewBox="0 0 22 22" aria-hidden="true"><circle cx="11" cy="11" r="9.5" fill="none" stroke="#999" stroke-width="2"/><path d="M13 6l-5 5 5 5" fill="none" stroke="#999" stroke-width="2"/></svg>
  <svg viewBox="0 0 22 22" aria-hidden="true"><circle cx="11" cy="11" r="9.5" fill="none" stroke="#999" stroke-width="2"/><path d="M9 6l5 5-5 5" fill="none" stroke="#999" stroke-width="2"/></svg>
</div>
<article class="abs news-item" style="left:74px">
  <div class="news-photo" role="img" aria-label="State enforcement office wall sign with official seals" style="background:linear-gradient(#c9c36a,#9aa04a)"></div>
  <div class="news-body">
    <p>Duis aliquam nibh a dui iaculis viverra id a velit. Vivamus egestas risus in magna varius commodo. Sed semper viverra egestas vel ornare...</p>
    <span class="btn">Read more</span>
  </div>
</article>
<article class="abs news-item" style="left:614px">
  <div class="news-photo" role="img" aria-label="Close-up of a cannabis flower on a dark background" style="background:radial-gradient(circle,#6f8f3a,#24321a 75%)"></div>
  <div class="news-body">
    <p>Duis aliquam nibh a dui iaculis viverra id a velit. Vivamus egestas risus in magna varius commodo. Sed semper viverra egestas vel ornare...</p>
    <span class="btn">Read more</span>
  </div>
</article>

<footer class="abs footer">
  <div class="footer-brand"><span class="brand-mark"></span><span class="brand-name">Harbor Crest</span></div>
  <p class="legal">Copyright © 2016. Company Name All Right Reserved<br>Terms Of Services &nbsp;|&nbsp; Privacy Policy</p>
  <div class="foot-nav">
    <h4>Navigation</h4>
    <div class="foot-cols">
      <ul>
        <li>Home</li><li>About us</li><li>Our staff</li>
        <li>MMJ trasnport &amp; Courier services</li><li>Our vehicles</li><li>Alarm systems</li>
      </ul>
      <ul>
        <li>Video systems</li><li>Video monitoring</li><li>Private investigations</li>
        <li>Surveillance audit</li><li>Compliance investigations</li><li>Contact us</li>
      </ul>
    </div>
  </div>
  <div class="connect">
    <h4>Connect us</h4>
    <div class="social" aria-label="Social links"><span></span><span></span><span></span><span></span><span></span></div>
  </div>
</footer>

</body>
</html>
```